Brookvale Building Company - advertisement poster

I am looking to print some canvas signs to advertise my general contracting company, Brookvale Building Company. The sign will measure 6' long x 3' high so the size should match that ratio. I already have a logo icon, which is the Letter 'B' and some trees that I would like to incorporate, see attached. I would also like the to have the following information listed:
1) phone number: 831-555-0172
2) email: brookvalebuildingcompany@mailnest.example
3) website: brookvalebuildingcompany.example
4) Lic#4826130
5) I want to use this text: "BUILD WITH THE B-CREW!"

The ad should be relatively simple and clean. Black and Green are my company colors. I am open to creative ideas!

Target Market(s)

People looking to renovate their homes

Industry/Entity Type

Construction

Colors
59FF00
82FF00
B8FF75
E3FFCB
F4FFEA

Requirements
Must have
• Must have my company logo
Should not have
• No photos or complex graphics

```html
<!DOCTYPE html>
<html lang="en">
<head>
<meta charset="utf-8">
<title>Brookvale Building Company – Sign</title>
<link rel="stylesheet" href="https://fonts.googleapis.com/css2?family=Montserrat:wght@500;600;700;800&display=swap">
<style>
  :root {
    --stage: #2b3038;
    --navy: #1f2470;
    --green: #7ccb3f;
    --lime-light: #bde79a;
    --mint: #d6f0dc;
    --sea: #a9dcb6;
  }
  * { margin: 0; padding: 0; box-sizing: border-box; }
  html, body {
    width: 1200px; height: 800px; overflow: hidden;
    background: var(--stage);
    font-family: "Montserrat", sans-serif;
  }
  body { position: relative; }
  .sign {
    position: absolute; left: 30px; top: 115px;
    width: 1140px; height: 570px;
    overflow: hidden;
    background:
      radial-gradient(ellipse 55% 60% at 55% 65%, var(--mint) 0%, rgba(214,240,220,0) 70%),
      linear-gradient(160deg, var(--lime-light) 0%, #c4eaa6 45%, var(--sea) 100%);
    color: var(--navy);
  }
  .brand {
    position: absolute; left: 160px; right: 0; top: 70px;
    display: flex; justify-content: center; align-items: center; gap: 14px;
  }
  .brand-mark { width: 26px; height: 26px; background: var(--green); flex: none; }
  .brand-name {
    font-weight: 700; font-size: 32px; letter-spacing: 0.08em; color: var(--navy);
    white-space: nowrap;
  }
  .headline-lead {
    position: absolute; left: 160px; right: 0; top: 190px; text-align: center;
    font-weight: 600; font-size: 50px; letter-spacing: 0.04em; white-space: nowrap;
  }
  .headline-main {
    position: absolute; left: 100px; right: 0; top: 250px; text-align: center;
    font-weight: 800; font-size: 124px; letter-spacing: 0.14em; line-height: 1;
    white-space: nowrap;
  }
  .phone {
    position: absolute; left: 80px; top: 450px; width: 320px; height: 60px;
    background: var(--navy); border-radius: 8px;
    display: flex; align-items: center; justify-content: center; gap: 16px;
    color: var(--green); font-weight: 600; font-size: 34px; letter-spacing: 0.02em;
  }
  .phone svg { width: 28px; height: 28px; }
  .license {
    position: absolute; left: 80px; width: 320px; top: 522px; text-align: center;
    font-weight: 500; font-size: 17px; letter-spacing: 0.03em;
  }
  .contact {
    position: absolute; top: 452px;
    font-weight: 600; font-size: 18px; letter-spacing: 0.02em;
  }
  .contact-line { display: flex; align-items: center; gap: 8px; white-space: nowrap; }
  .contact-line svg { width: 20px; height: 20px; flex: none; }
  .contact-tag {
    display: inline-block; margin: 8px 0 0 28px; padding: 2px 10px;
    background: var(--navy); color: #ffffff; border-radius: 3px;
    font-size: 15px; font-weight: 500;
  }
  .contact-web { left: 470px; }
  .contact-mail { left: 812px; }
</style>
</head>
<body>
  <main class="sign">
    <div class="brand">
      <span class="brand-mark"></span>
      <span class="brand-name">BROOKVALE BUILDING COMPANY</span>
    </div>

    <p class="headline-lead">BUILD WITH THE</p>
    <h1 class="headline-main">B-CREW!</h1>

    <div class="phone">
      <svg viewBox="0 0 24 24" fill="none" stroke="currentColor" stroke-width="2" stroke-linecap="round" stroke-linejoin="round" aria-hidden="true">
        <path d="M5 3h3l2 5-2.5 1.5a11 11 0 0 0 6 6L15 13l5 2v3a2 2 0 0 1-2 2A16 16 0 0 1 3 5a2 2 0 0 1 2-2z"/>
        <path d="M15 3a6 6 0 0 1 6 6"/>
        <path d="M15 7a2 2 0 0 1 2 2"/>
      </svg>
      <span>831.555.0172</span>
    </div>
    <p class="license">License Number: 4826130</p>

    <div class="contact contact-web">
      <div class="contact-line">
        <svg viewBox="0 0 24 24" fill="none" stroke="currentColor" stroke-width="1.8" aria-hidden="true">
          <circle cx="12" cy="12" r="9"/>
          <ellipse cx="12" cy="12" rx="4" ry="9"/>
          <path d="M3 12h18M5 7h14M5 17h14"/>
        </svg>
        <span>BrookvaleBuildingCompany</span>
      </div>
      <span class="contact-tag">.example</span>
    </div>

    <div class="contact contact-mail">
      <div class="contact-line">
        <svg viewBox="0 0 24 24" aria-hidden="true">
          <rect x="3" y="6" width="18" height="12" rx="1" fill="currentColor"/>
          <path d="M3.5 6.5 12 13l8.5-6.5" fill="none" stroke="#d6f0dc" stroke-width="1.6"/>
        </svg>
        <span>BrookvaleBuildingCompany</span>
      </div>
      <span class="contact-tag">@mailnest.example</span>
    </div>
  </main>
</body>
</html>
```